Website for virtual assistant and proofreader

Professional, feminine (but not flowery!) website offering and explaining my services as a VA and Proofreader. Probably only 7 pages: home, about, services (x2), fees, testimonials and contact page. <br/><br/>I already have most of the content, which I have uploaded so you can get an idea of waht I do. I have brand colours and logo already also uploaded. I really just need the bones of the site to be designed and am happy/capable of setting this up as a Wordpress site. I'm just rubbish at design!

Industry/Entity Type

Business Service

Coding

Coded - Design and coding required

Number of Pages Required

4 page

Other font styles liked:
• Roboto Bold + Great Vibes

Colors
3276b5
fee3d4

Requirements
Must have
• should be informative, professional, feminine. Clean, clear, CTA's links to services and fees pages
• Also, see all 3 colour codes on the attached doc.
Nice to have
• business images but place holders will do
Should not have
• Nothing flowery or cartoons! Not 'busy'

```html
<!DOCTYPE html>
<html lang="en">
<head>
<meta charset="utf-8">
<title>Marla J Reeve – Virtual Assistant and Proofreader</title>
<link rel="stylesheet" href="https://fonts.googleapis.com/css2?family=Roboto:wght@300;400;500;700&family=Great+Vibes&family=Playball&display=swap">
<style>
:root{
  --blue:#155f8c;
  --blue-deep:#165d88;
  --pink:#f2c4b1;
  --pink-soft:#f6d3c4;
  --cream:#fef8f1;
  --taupe:#8c817e;
  --ink:#3a3a3a;
  --grey:#888;
  --white:#fff;
}
*{box-sizing:border-box;margin:0;padding:0}
html,body{width:1200px;height:3133px;overflow:hidden}
body{position:relative;background:var(--white);font-family:'Roboto',sans-serif;color:var(--ink)}
.abs{position:absolute}
.script{font-family:'Great Vibes',cursive;font-weight:400}
.btn{position:absolute;display:flex;align-items:center;justify-content:center;gap:8px;background:var(--blue);color:var(--white);font-weight:700;text-transform:uppercase;border-radius:2px;text-decoration:none}
.btn svg{flex:none}

.topbar{position:absolute;left:0;top:0;width:1200px;height:5px;background:linear-gradient(90deg,var(--blue) 50%,#8c817e 50%)}
.bottombar{position:absolute;left:0;top:3125px;width:1200px;height:8px;background:linear-gradient(90deg,var(--blue) 50%,#8c817e 50%)}

/* hero */
.hero{position:absolute;left:0;top:5px;width:1200px;height:627px;background:linear-gradient(100deg,#fbf9f6 0%,#f7efe6 35%,#efd9c3 60%,#e2d8cf 80%,#d9dde2 100%)}
.brand{position:absolute;left:143px;top:60px;display:flex;align-items:center;gap:10px}
.brand-dot{width:34px;height:34px;border-radius:50%;background:var(--blue)}
.brand-name{font-size:22px;font-weight:500;color:var(--blue);line-height:1}
.brand-sub{position:absolute;left:187px;top:110px;font-size:11px;color:#555}
.nav{position:absolute;top:80px;left:502px;display:flex;align-items:center;font-size:13px;text-transform:uppercase;color:#333}
.nav a{color:inherit;text-decoration:none;margin-right:24px}
.nav a.active{background:var(--blue);color:var(--white);padding:8px 16px;border-radius:2px;margin-right:18px}
.hero-title{left:138px;top:235px;font-size:86px;color:var(--blue);line-height:1}
.hero-text{left:142px;top:365px;font-size:28px;line-height:38px;color:#333;width:450px}
.chev{left:590px;top:620px}

/* about */
.portrait{left:146px;top:699px;width:414px;height:414px;border-radius:50%;border:18px solid var(--pink-soft)}
.portrait-photo{left:165px;top:718px;width:376px;height:376px;border-radius:50%;background:radial-gradient(circle at 50% 45%,#d9a78a,#a8674a 60%,#6f4636)}
.about-script{left:616px;top:682px;font-size:76px;color:var(--blue);line-height:1}
.about-name{left:619px;top:773px;font-size:60px;font-weight:500;color:#4a4a4a}
.about-text{left:621px;top:857px;width:435px;font-size:13.5px;line-height:26.5px;color:#8a8a8a;font-weight:300}

/* services */
.services{position:absolute;left:0;top:1204px;width:1200px;height:830px;background:var(--cream)}
.sec-title{position:absolute;left:0;width:1200px;text-align:center;font-size:60px;font-weight:500;color:#4a4a4a}
.sec-title .script{color:var(--blue);font-size:74px;margin-right:12px}
.sec-text{position:absolute;left:200px;width:800px;text-align:center;font-size:13.5px;line-height:26.5px;color:#8a8a8a;font-weight:300}
.card{position:absolute;top:1548px;width:218px;height:276px;background:var(--white);box-shadow:0 2px 6px rgba(0,0,0,.05);text-align:center}
.card-icon{position:absolute;left:84px;top:20px;width:50px;height:68px;border:2px solid var(--blue);border-radius:4px;background:#eaf2f8}
.card h3{position:absolute;left:0;top:102px;width:100%;font-size:13.5px;line-height:20px;font-weight:500;color:#333;text-transform:uppercase}
.card p{position:absolute;left:22px;top:154px;width:174px;font-size:13.5px;line-height:19.5px;color:#999;font-weight:300}
.card .btn{left:48px;top:228px;width:122px;height:31px;font-size:12.5px}
.motto{position:absolute;left:0;top:1885px;width:1200px;text-align:center;font-family:'Playball',cursive;font-size:36px;color:#333}

/* why me */
.why{position:absolute;left:108px;top:2034px;width:984px;height:371px;background:var(--taupe);z-index:2}
.acc-open{position:absolute;left:63px;top:68px;width:418px;height:207px;background:var(--white)}
.acc-head{height:48px;background:var(--blue);color:var(--white);font-size:13.5px;font-weight:500;display:flex;align-items:center;justify-content:space-between;padding:0 18px 0 22px;text-transform:uppercase}
.acc-body{padding:22px 20px;font-size:13.5px;line-height:21.5px;color:#888;font-weight:300}
.acc-item{position:absolute;left:504px;width:416px;height:47px;background:var(--white);font-size:13.5px;color:#666;display:flex;align-items:center;justify-content:space-between;padding:0 18px 0 22px;text-transform:uppercase}

/* testimonials */
.testi{position:absolute;left:0;top:2377px;width:1200px;height:414px;background:var(--blue-deep)}
.testi-title{position:absolute;left:0;top:2460px;width:1200px;text-align:center;font-size:64px;font-weight:500;color:var(--pink)}
.testi-title .script{color:var(--white);font-size:82px;margin-right:8px}
.avatar{position:absolute;width:108px;height:108px;border-radius:50%;background:radial-gradient(circle at 50% 40%,#c9a98f,#6f7d52 70%)}
.quote{position:absolute;top:2600px;width:300px;font-size:11.5px;line-height:18.5px;color:var(--white);font-style:italic;font-weight:300}
.quote b{display:block;margin-top:8px;font-style:normal;font-weight:700;font-size:12.5px}

/* footer */
.social{position:absolute;top:2871px;width:46px;height:46px;border-radius:50%;border:2px solid var(--pink-soft);display:flex;align-items:center;justify-content:center}
.social span{width:10px;height:10px;border-radius:50%;background:var(--blue)}
.foot-nav{position:absolute;left:0;top:2948px;width:1200px;display:flex;justify-content:center;gap:30px;font-size:16.5px;color:#333;text-transform:uppercase}
.foot-contact{position:absolute;left:0;top:2992px;width:1200px;display:flex;justify-content:center;align-items:center;gap:10px;font-size:13.5px;color:#666}
.foot-contact .sep{color:#999}
.copy{position:absolute;left:0;top:3031px;width:1200px;text-align:center;font-size:13.5px;color:#666}
</style>
</head>
<body>
<div class="topbar"></div>

<section class="hero" role="img" aria-label="Photo of hands typing on a laptop keyboard at a bright desk"></section>
<div class="brand"><span class="brand-dot"></span><span class="brand-name">Marla J Reeve</span></div>
<div class="abs brand-sub">Virtual Assistant and Proofreader</div>
<nav class="nav">
  <a class="active" href="#">Home</a><a href="#">Services</a><a href="#">System Applications</a><a href="#">Fees</a><a href="#">Why me?</a><a href="#">Contact</a>
</nav>
<h1 class="abs hero-title script">Allow Me...</h1>
<p class="abs hero-text">To handle the details so you can get on with business.</p>
<a class="btn" href="#" style="left:142px;top:478px;width:153px;height:40px;font-size:16px">Contact
  <svg width="14" height="14" viewBox="0 0 14 14"><circle cx="7" cy="7" r="7" fill="#fff"/><path d="M5 3.5 8.5 7 5 10.5" stroke="#155f8c" stroke-width="2" fill="none"/></svg></a>
<svg class="abs chev" width="20" height="10" viewBox="0 0 20 10"><path d="M2 1 10 8 18 1" stroke="#999" stroke-width="1.5" fill="none"/></svg>

<div class="abs portrait"></div>
<div class="abs portrait-photo" role="img" aria-label="Portrait photo of the virtual assistant"></div>
<div class="abs about-script script">About</div>
<h2 class="abs about-name">Marla J Reeve</h2>
<p class="abs about-text">Every great leader is backed by diligent and knowledgeable support. Have you ever wondered what it would be like to have your very own personal assistant? Well, you can. A virtual assistant can do everything a full-time assistant can, with the added bonus that she can save you money. Whether you need daily help, or help with special assignments or big projects, hiring me as your VA will save you the costs typically associated with an employee–holiday pay</p>
<a class="btn" href="#" style="left:621px;top:1071px;width:153px;height:40px;font-size:14.5px">Learn more
  <svg width="13" height="13" viewBox="0 0 14 14"><circle cx="7" cy="7" r="7" fill="#fff"/><path d="M5 3.5 8.5 7 5 10.5" stroke="#155f8c" stroke-width="2" fill="none"/></svg></a>

<section class="services"></section>
<h2 class="sec-title" style="top:1300px"><span class="script">Our</span>Services</h2>
<p class="sec-text" style="top:1408px">Do you need some Smart Office Support (SOS)? Do you have a huge project looming on the horizon? Do you just need a little support managing the growing stacks of To-Dos cluttering your desk? As a master of managing the barrage of daily details that require concise and prompt attention, SOS is my speciality, from organisation to proofreading, no detail is too small!</p>

<div class="card" style="left:145px"><div class="card-icon" role="img" aria-label="Project planning icon"></div><h3>Organizational/<br>Project Management</h3><p>Reliable project and team management, master of organisation</p><a class="btn" href="#">Learn more <svg width="11" height="11" viewBox="0 0 14 14"><circle cx="7" cy="7" r="7" fill="#fff"/><path d="M5 3.5 8.5 7 5 10.5" stroke="#155f8c" stroke-width="2" fill="none"/></svg></a></div>
<div class="card" style="left:376px"><div class="card-icon" role="img" aria-label="Administrative support icon"></div><h3>Administrative and<br>Accounting Support</h3><p>Work smarter not harder with the right VA by your side</p><a class="btn" href="#">Learn more <svg width="11" height="11" viewBox="0 0 14 14"><circle cx="7" cy="7" r="7" fill="#fff"/><path d="M5 3.5 8.5 7 5 10.5" stroke="#155f8c" stroke-width="2" fill="none"/></svg></a></div>
<div class="card" style="left:607px"><div class="card-icon" role="img" aria-label="Website administration icon"></div><h3>Website<br>Admininstration</h3><p>Dependable and reliable website updates–like clockwork</p><a class="btn" href="#">Learn more <svg width="11" height="11" viewBox="0 0 14 14"><circle cx="7" cy="7" r="7" fill="#fff"/><path d="M5 3.5 8.5 7 5 10.5" stroke="#155f8c" stroke-width="2" fill="none"/></svg></a></div>
<div class="card" style="left:838px"><div class="card-icon" role="img" aria-label="Editorial service icon"></div><h3>Editorial Service/<br>Proofreading</h3><p>Catching simple typos and grammatical faux pas to preserve your integrity</p><a class="btn" href="#">Learn more <svg width="11" height="11" viewBox="0 0 14 14"><circle cx="7" cy="7" r="7" fill="#fff"/><path d="M5 3.5 8.5 7 5 10.5" stroke="#155f8c" stroke-width="2" fill="none"/></svg></a></div>

<p class="motto">If you want something done right... find the right person to do it!</p>

<section class="why">
  <div class="acc-open">
    <div class="acc-head">Why me?<svg width="13" height="13" viewBox="0 0 14 14"><circle cx="7" cy="7" r="7" fill="#fff"/><rect x="3.5" y="6" width="7" height="2" fill="#155f8c"/></svg></div>
    <div class="acc-body">I offer administrative, management, and editorial services for those in need of an expert,professional, and discreet “virtual” assistant. As an independent contractor, I can offer you these services with all the same dedication and loyalty as a full-time staff assistant – at a more cost-effective rate.</div>
  </div>
  <div class="acc-item" style="top:68px">Who’s benefited from my help...<svg width="13" height="13" viewBox="0 0 14 14"><circle cx="7" cy="7" r="7" fill="#155f8c"/><path d="M3.5 7h7M7 3.5v7" stroke="#fff" stroke-width="2"/></svg></div>
  <div class="acc-item" style="top:122px">What I can do for you...<svg width="13" height="13" viewBox="0 0 14 14"><circle cx="7" cy="7" r="7" fill="#155f8c"/><path d="M3.5 7h7M7 3.5v7" stroke="#fff" stroke-width="2"/></svg></div>
  <div class="acc-item" style="top:175px">Sometimes your calling... well, it finds you!<svg width="13" height="13" viewBox="0 0 14 14"><circle cx="7" cy="7" r="7" fill="#155f8c"/><path d="M3.5 7h7M7 3.5v7" stroke="#fff" stroke-width="2"/></svg></div>
  <div class="acc-item" style="top:229px">Certifications and qualifications<svg width="13" height="13" viewBox="0 0 14 14"><circle cx="7" cy="7" r="7" fill="#155f8c"/><path d="M3.5 7h7M7 3.5v7" stroke="#fff" stroke-width="2"/></svg></div>
</section>

<section class="testi"></section>
<h2 class="testi-title"><span class="script">Client</span>Testimonials</h2>
<svg class="abs" style="left:80px;top:2616px" width="34" height="64" viewBox="0 0 34 64"><path d="M32 2 2 32 32 62" stroke="#fff" stroke-width="1.5" fill="none"/></svg>
<svg class="abs" style="left:1088px;top:2616px" width="34" height="64" viewBox="0 0 34 64"><path d="M2 2 32 32 2 62" stroke="#fff" stroke-width="1.5" fill="none"/></svg>
<div class="avatar" style="left:151px;top:2594px" role="img" aria-label="Client photo"></div>
<p class="quote" style="left:278px">@MarlaReeve,·Oct 24, 2018<br>Burnout can creep up on you when you least expect it. One way to counteract this is to hire a #freelancer or #VA to take on some of your tas<b>- Marla J Reeve - VA &amp; Proofreader</b></p>
<div class="avatar" style="left:638px;top:2594px" role="img" aria-label="Client photo"></div>
<p class="quote" style="left:764px">@MarlaReeve,·Oct 24, 2018<br>Burnout can creep up on you when you least expect it. One way to counteract this is to hire a #freelancer or #VA to take on some of your tas<b>- Marla J Reeve - VA &amp; Proofreader</b></p>

<div class="social" style="left:493px"><span></span></div>
<div class="social" style="left:546px"><span></span></div>
<div class="social" style="left:601px"><span></span></div>
<div class="social" style="left:654px"><span></span></div>
<nav class="foot-nav"><span>Home</span><span>Services</span><span>System Applications</span><span>Fees</span><span>Why me?</span><span>Contact</span></nav>
<div class="foot-contact">
  <svg width="10" height="14" viewBox="0 0 10 14"><path d="M5 0a5 5 0 0 1 5 5c0 4-5 9-5 9S0 9 0 5a5 5 0 0 1 5-5z" fill="#f2c4b1"/><circle cx="5" cy="5" r="2" fill="#fff"/></svg>
  <span>Box 4410, 2180 Harbour Lane Westby</span><span class="sep">|</span>
  <svg width="13" height="13" viewBox="0 0 13 13"><path d="M3 0l2 3-1.5 1.5a8 8 0 0 0 5 5L10 8l3 2-1.5 3C5 13 0 8 0 1.5z" fill="#f2c4b1"/></svg>
  <span>1 800 555 0142</span><span class="sep">|</span>
  <svg width="15" height="11" viewBox="0 0 15 11"><rect width="15" height="11" rx="1" fill="#f2c4b1"/><path d="M1 1l6.5 5L14 1" stroke="#fff" fill="none"/></svg>
  <span>hello@deskwise-va.com</span>
</div>
<p class="copy">Marla J Reeve - VA &amp; Proofreader © 2020 . All rights reserved.</p>

<div class="bottombar"></div>
</body>
</html>
```